Verdana Crest New Website - Online Learning and Education

New Wordpress website for an online learning site that has courses, worksheets, quizzes, etc.
Updates

We would like something similar to this website: https://hallowaybridgeinstitute.example/mediation-skills-course/. But continue with the content of our current website: http://verdanacrestlearninghub.example

We would like something similar to this site: https://hallowaybridgeinstitute.example/mediation-skills-course/

Coding

Coded - Design and coding required

```html
<!DOCTYPE html>
<html lang="en">
<head>
<meta charset="utf-8">
<title>Verdana Crest – Online Learning</title>
<link href="https://fonts.googleapis.com/css2?family=Montserrat:wght@500;600;700;800&family=Lato:wght@400;700&family=Roboto:wght@400;500;700&display=swap" rel="stylesheet">
<style>
:root{
  --red:#c41e35;
  --red-dark:#a8182c;
  --blue:#1e4d8c;
  --blue-deep:#183f75;
  --ink:#2b2b2b;
  --muted:#777;
  --line:#e3e3e3;
  --white:#fff;
}
*{margin:0;padding:0;box-sizing:border-box}
html,body{width:1200px;height:5133px;overflow:hidden}
body{position:relative;font-family:"Roboto",Arial,sans-serif;color:var(--ink);background:#fff}
.abs{position:absolute}
a{color:inherit;text-decoration:none}
.btn{position:absolute;display:flex;align-items:center;justify-content:center;gap:7px;background:var(--red);color:#fff;font:700 14px "Roboto",Arial,sans-serif;border-radius:24px;text-transform:uppercase}
.btn .dot{width:13px;height:13px;border-radius:50%;background:#fff;position:relative}
.btn .dot::after{content:"";position:absolute;left:4px;top:3px;border-left:6px solid var(--red);border-top:3.5px solid transparent;border-bottom:3.5px solid transparent}

/* top bar */
.topbar{top:0;left:0;width:1200px;height:46px;background:var(--red);color:#fff;font-size:13px}
.topbar span{position:absolute;top:15px}
/* header */
.header{top:46px;left:0;width:1200px;height:144px;background:#fff}
.brand{position:absolute;display:flex;align-items:center;gap:12px;font-family:"Montserrat",sans-serif;font-weight:700}
.brand .mark{border-radius:50%}
.nav{position:absolute;top:62px;right:112px;display:flex;gap:26px;font:600 15px "Montserrat",sans-serif;color:#222}
/* hero */
.hero-photo{top:190px;left:0;width:1200px;height:760px;background:linear-gradient(100deg,#c9c2b6 0%,#9aa5b2 25%,#d7c7ae 55%,#8a6b4e 80%,#b69a78 100%)}
.hero-box{top:382px;left:590px;width:476px;height:248px;background:rgba(210,210,214,.55)}
.hero-box .name{position:absolute;left:40px;top:30px;font:700 40px "Montserrat",sans-serif;color:#fff;letter-spacing:1px}
.hero-box p{position:absolute;left:40px;top:96px;width:420px;font-size:15px;line-height:24px;color:#fff}
/* online learning */
.ol-title{top:920px;width:1200px;text-align:center;font:800 40px "Montserrat",sans-serif;color:#fff}
.ol-lead{top:1000px;left:200px;width:800px;text-align:center;color:#fff;font-size:15px;line-height:31px}
.feature{position:absolute;top:1110px;width:232px;text-align:center;color:#fff}
.feature svg{display:block;margin:0 auto 12px}
.feature h3{font:500 16px "Roboto",sans-serif;text-transform:uppercase;margin-bottom:10px}
.feature p{font-size:13.5px;line-height:26px}
/* welcome */
.welcome-bg{top:1500px;left:0;width:1200px;height:1100px;background:linear-gradient(180deg,#fff 0%,#f4f5f8 40%,#eef0f4 80%,#fff 100%)}
.welcome-title{top:1760px;width:1200px;text-align:center;font:800 40px "Montserrat",sans-serif;color:#2d2d2d}
.welcome-text{top:1848px;left:180px;width:840px;text-align:center;color:#777;font-size:14.5px;line-height:34px}
.card{position:absolute;top:2040px;width:298px;height:412px;background:#fff;border-bottom:3px solid var(--red);box-shadow:0 2px 8px rgba(0,0,0,.08)}
.card .ph{height:196px}
.card h3{margin:30px 24px 12px;font:400 23px "Lato",sans-serif;color:#222}
.card p{margin:0 24px;font-size:14px;line-height:26px;color:#777;text-align:justify}
.card .more{position:absolute;left:24px;bottom:30px;font:700 13px "Roboto",sans-serif;color:var(--red);display:flex;align-items:center;gap:5px}
.more .dot{width:12px;height:12px;border-radius:50%;background:var(--red);position:relative}
.more .dot::after{content:"";position:absolute;left:4px;top:3px;border-left:5px solid #fff;border-top:3px solid transparent;border-bottom:3px solid transparent}
/* stats */
.why-title{top:2700px;width:1200px;text-align:center;font:800 40px "Montserrat",sans-serif;color:#fff}
.stat{position:absolute;top:2805px;width:260px;text-align:center;color:#fff}
.stat b{display:block;font:700 60px "Montserrat",sans-serif;line-height:70px}
.stat span{display:block;margin-top:18px;font:600 21px "Montserrat",sans-serif;text-transform:uppercase}
/* ways */
.ways-title{top:3170px;left:604px;font:800 42px "Montserrat",sans-serif;color:#2d2d2d;letter-spacing:1px}
.ways-text{left:604px;width:486px;color:#777;font-size:15px;line-height:29px;text-align:justify}
.divider{top:3718px;left:112px;width:976px;height:1px;background:#dcdcdc}
/* articles */
.art-title{top:3818px;width:1200px;text-align:center;font:800 42px "Montserrat",sans-serif;color:#2d2d2d}
.big-art{top:3930px;left:106px;width:480px;height:436px;background:#fff;box-shadow:0 2px 8px rgba(0,0,0,.1)}
.big-art .ph{height:290px}
.date-tag{position:absolute;top:38px;right:30px;width:42px;height:54px;background:var(--blue);color:#fff;text-align:center;font:700 11px "Roboto",sans-serif;padding-top:6px}
.date-tag b{display:block;font-size:19px;margin-top:2px}
.big-art h3{margin:34px 20px 10px;font:500 20px "Roboto",sans-serif;color:#222}
.big-art p{margin:0 20px;font-size:12.5px;line-height:24px;color:#888}
.mini-art{position:absolute;left:624px;width:468px;height:196px;background:#fff;box-shadow:0 2px 8px rgba(0,0,0,.1)}
.mini-art .ph{position:absolute;left:0;top:0;width:168px;height:196px}
.mini-art .body{position:absolute;left:194px;top:24px;width:260px}
.mini-art h4{font:500 16px "Roboto",sans-serif;line-height:23px;color:#222}
.mini-art .date{margin:8px 0;font:500 12px "Roboto",sans-serif;color:var(--blue)}
.mini-art p{font-size:11.5px;line-height:22px;color:#888}
/* footer */
.foot-col{position:absolute;top:4826px;color:#fff}
.foot-col h5{font:600 15px "Roboto",sans-serif;text-transform:uppercase;margin-bottom:24px}
.foot-col li{list-style:none;font-size:13px;line-height:30px;display:flex;gap:14px}
.foot-col li i{font-style:normal;color:#cfd8e6}
.contact-row{display:flex;gap:18px;font-size:13px;line-height:19px;margin-bottom:26px}
.email-field{width:248px;height:34px;border:1px solid rgba(255,255,255,.7);font-size:11px;padding:11px 12px;margin:18px 0 20px}
.sub-btn{display:inline-block;background:var(--red);color:#fff;font:700 12px "Roboto",sans-serif;padding:10px 20px;border-radius:20px}
.foot-line{top:5053px;left:112px;width:976px;height:1px;background:rgba(255,255,255,.4)}
.copy{top:5090px;left:112px;color:#fff;font-size:14px}
.socials{top:5076px;left:914px;display:flex;gap:10px}
.socials span{width:36px;height:36px;border:2px solid #fff;border-radius:50%;display:block}
</style>
</head>
<body>

<!-- Top bar -->
<div class="abs topbar">
  <span style="left:112px">&#9742; (+1) 555 014 2290</span>
  <span style="left:286px">&#9993; info@verdanacrest.example</span>
  <span style="left:808px;font-weight:700">&#9998; APPLY</span>
  <span style="left:896px;font-weight:700">&#9906; VISIT</span>
  <span style="left:972px;font-weight:700">&#9432; REQUEST INFO</span>
</div>

<!-- Header -->
<header class="abs header">
  <div class="brand" style="left:112px;top:44px;color:var(--blue);font-size:32px">
    <span class="mark" style="width:34px;height:34px;background:var(--blue)"></span>Verdana Crest
  </div>
  <nav class="nav"><a>HOME</a><a>COURSES</a><a>NEWS</a><a>ABOUT US</a><a>CONTACT US</a>
    <svg width="16" height="16" viewBox="0 0 16 16"><circle cx="6.5" cy="6.5" r="5" fill="none" stroke="#222" stroke-width="2"/><line x1="10" y1="10" x2="15" y2="15" stroke="#222" stroke-width="2.4"/></svg>
  </nav>
</header>

<!-- Hero -->
<div class="abs hero-photo" role="img" aria-label="Photo of a student at a desk thinking while studying on a laptop in a bright café"></div>
<div class="abs hero-box">
  <div class="name">Verdana Crest</div>
  <p>Nemo enim ipsam voluptatem quia voluptas sit sed quia aspernatur aut odit aut fugit.</p>
  <div class="btn" style="left:40px;top:162px;width:176px;height:44px">Read more <span class="dot"></span></div>
</div>

<!-- Curved bands -->
<svg class="abs" style="top:0;left:0" width="1200" height="5133" viewBox="0 0 1200 5133">
  <!-- online learning band -->
  <path d="M0,910 Q600,730 1200,910 L1200,1395 Q600,1525 0,1395 Z" fill="var(--blue)"/>
  <path d="M0,1400 Q600,1548 1200,1400 Q600,1600 0,1400 Z" fill="var(--red)"/>
  <!-- why choose band -->
  <path d="M0,2660 Q600,2520 1200,2660 Q600,2545 0,2660 Z" fill="var(--blue)"/>
  <path d="M0,2665 Q600,2555 1200,2665 L1200,2950 Q600,3050 0,2950 Z" fill="var(--red)"/>
  <path d="M0,2955 Q600,3060 1200,2955 Q600,3100 0,2955 Z" fill="var(--blue)"/>
  <!-- footer band -->
  <path d="M0,4680 Q600,4525 1200,4680 Q600,4555 0,4680 Z" fill="var(--red)"/>
  <path d="M0,4690 Q600,4560 1200,4690 L1200,5133 L0,5133 Z" fill="var(--blue)"/>
</svg>

<!-- Online learning -->
<h2 class="abs ol-title">ONLINE LEARNING</h2>
<p class="abs ol-lead">Lorem ipsum dolor sit amet, consectetur adipiscing elit, sed do eiusmod tempor incididunt ut labore et dolore magna aliqua. Ut enim ad minim veniam, quis nostrud exercitation ullamco laboris.</p>

<div class="feature" style="left:106px">
  <svg width="72" height="64" viewBox="0 0 72 64" fill="none" stroke="#fff" stroke-width="2.5"><rect x="6" y="18" width="46" height="34"/><rect x="12" y="12" width="46" height="34"/><rect x="18" y="6" width="46" height="34"/><circle cx="29" cy="35" r="9"/><path d="M26,30 L34,35 L26,40 Z"/></svg>
  <h3>Find a course</h3><p>Lorem ipsum dolor sit amet, con sectetur adipiscing elit.</p>
</div>
<div class="feature" style="left:358px">
  <svg width="72" height="64" viewBox="0 0 72 64" fill="none" stroke="#fff" stroke-width="2.5"><rect x="14" y="22" width="44" height="34"/><path d="M22,14 L36,6 L50,14 L36,20 Z"/><path d="M30,32 L42,39 L30,46 Z"/><line x1="8" y1="58" x2="64" y2="58"/></svg>
  <h3>Go online</h3><p>Lorem ipsum dolor sit amet, con sectetur adipiscing elit.</p>
</div>
<div class="feature" style="left:610px">
  <svg width="72" height="64" viewBox="0 0 72 64" fill="none" stroke="#fff" stroke-width="2.5"><path d="M26,8 L40,8 L36,16 L30,16 Z"/><path d="M30,16 Q10,30 16,50 Q20,58 34,58 Q48,58 50,48"/><circle cx="54" cy="48" r="10"/><line x1="40" y1="34" x2="62" y2="34"/><line x1="40" y1="28" x2="62" y2="28"/></svg>
  <h3>Worried about cost?</h3><p>Lorem ipsum dolor sit amet, con sectetur adipiscing elit.</p>
</div>
<div class="feature" style="left:862px">
  <svg width="72" height="64" viewBox="0 0 72 64" fill="none" stroke="#fff" stroke-width="2.5"><rect x="10" y="8" width="50" height="40"/><line x1="18" y1="18" x2="50" y2="18"/><line x1="18" y1="26" x2="42" y2="26"/><line x1="18" y1="34" x2="36" y2="34"/><circle cx="48" cy="40" r="8"/><path d="M44,47 L42,58 L48,54 L54,58 L52,47"/></svg>
  <h3>Certificates</h3><p>Lorem ipsum dolor sit amet, con sectetur adipiscing elit.</p>
</div>
<div class="btn" style="left:504px;top:1324px;width:192px;height:46px">Learn more <span class="dot"></span></div>

<!-- Welcome -->
<div class="abs welcome-bg" role="img" aria-label="Faint background photo of a study desk"></div>
<div class="abs" style="top:1612px;left:564px;width:72px;height:72px;border-radius:50%;background:var(--blue)"></div>
<h2 class="abs welcome-title">WELCOME TO VERDANA CREST</h2>
<p class="abs welcome-text">Lorem ipsum dolor sit amet, consectetur adipiscing elit, sed do eiusmod tempor incididunt ut labore et dolore magna aliqua. Ut enim ad minim veniam, quis nostrud exercitation ullamco laboris nisi ut aliquip ex ea commodo consequat. Duis aute irure dolor in reprehenderit in voluptate velit esse cillum dolore eu fugiat nulla pariatur. Excepteur sint occaecat cupidatat non proident, sunt in culpa qui officia deserunt mollit anim.</p>

<article class="card" style="left:112px">
  <div class="ph" role="img" aria-label="Photo of a child watching a video lesson on a laptop" style="background:linear-gradient(135deg,#6b5a4c,#9a7a5d 50%,#c6805a)"></div>
  <h3>Worksheets</h3>
  <p>Lorem ipsum dolor sit amet consecte ture adipiscing elit, sed do eiusmod tempor incididunt labore...</p>
  <span class="more">READ MORE <span class="dot"></span></span>
</article>
<article class="card" style="left:450px">
  <div class="ph" role="img" aria-label="Photo of letter tiles spelling quiz on a white background" style="background:linear-gradient(135deg,#f2f2f2,#dcdcdc 50%,#8fc8c0 85%,#d8507a)"></div>
  <h3>Quizzes</h3>
  <p>Lorem ipsum dolor sit amet consecte ture adipiscing elit, sed do eiusmod tempor incididunt labore...</p>
  <span class="more">READ MORE <span class="dot"></span></span>
</article>
<article class="card" style="left:790px">
  <div class="ph" role="img" aria-label="Photo of hands typing on a laptop showing an online courses page" style="background:linear-gradient(135deg,#8d8a84,#5f5a52 45%,#d8d4cc)"></div>
  <h3>Online Learning</h3>
  <p>Lorem ipsum dolor sit amet consecte ture adipiscing elit, sed do eiusmod tempor incididunt labore...</p>
  <span class="more">READ MORE <span class="dot"></span></span>
</article>

<!-- Why choose us -->
<h2 class="abs why-title">WHY CHOOSE US?</h2>
<div class="stat" style="left:74px"><b>500+</b><span>Online courses</span></div>
<div class="stat" style="left:324px"><b>10</b><span>Online degrees</span></div>
<div class="stat" style="left:570px"><b>18</b><span>Online minors</span></div>
<div class="stat" style="left:840px"><b>50+</b><span>Online certificates</span></div>

<!-- Ways to learn -->
<div class="abs" style="top:3162px;left:98px;width:436px;height:440px;border-radius:50%;border-bottom:6px solid var(--red)"></div>
<div class="abs" role="img" aria-label="Photo of a smiling student wearing headphones studying at a laptop" style="top:3168px;left:104px;width:424px;height:424px;border-radius:50%;background:linear-gradient(135deg,#b7c3cf,#8aa0b6 45%,#d9d2c6)"></div>
<h2 class="abs ways-title">WAYS TO LEARN</h2>
<p class="abs ways-text" style="top:3254px">Lorem ipsum dolor sit amet, consectetur adipiscing elit, sed do eiusmod tempor incididunt ut labore et dolore magna aliqua.</p>
<p class="abs ways-text" style="top:3342px">Ut enim ad minim veniam, quis nostrud exercitation ullamco laboris nisi ut aliquip ex ea commodo consequat. Duis aute irure dolor in reprehenderit in voluptate velit esse cillum dolore eu fugiat nulla pariatur. Excepteur sint occaecat cupidatat non proident, sunt in culpa qui officia deserunt mollit anim id est laborum.</p>
<div class="btn" style="left:604px;top:3536px;width:194px;height:48px">Read more <span class="dot"></span></div>

<div class="abs divider"></div>

<!-- Latest articles -->
<h2 class="abs art-title">LATEST ARTICLES</h2>
<article class="abs big-art">
  <div class="ph" role="img" aria-label="Photo of a laptop showing an e-learning page beside a coffee cup" style="background:linear-gradient(135deg,#4a3a30,#9a8c80 45%,#e8e4de)"></div>
  <div class="date-tag">MAY<b>08</b></div>
  <h3>Lorem ipsum dolor sit, consectetur</h3>
  <p>At vero eos et accusamus et iusto odio dignissimos ducimus qui blanditiis praesentium voluptatum vobcb deleniti atque corrupti</p>
</article>
<article class="mini-art" style="top:3930px">
  <div class="ph" role="img" aria-label="Photo of a student with headphones working on a laptop" style="background:linear-gradient(135deg,#c9c9c9,#7d6a5c 50%,#e4e4e4)"></div>
  <div class="body">
    <h4>Nemo enim ipsam volutem odit voluptast aspernatur odit</h4>
    <div class="date">&#128197; Apr 28, 2019</div>
    <p>Neque porro quisquam est, qui dolorem ipsum quia dolor sit amet, consectetur, adipisci velit, sed quia non numquam eius modi</p>
  </div>
</article>
<article class="mini-art" style="top:4162px">
  <div class="ph" role="img" aria-label="Photo of a student writing notes at a desk" style="background:linear-gradient(135deg,#e0e0e0,#8a7060 50%,#cfcfcf)"></div>
  <div class="body">
    <h4>Nemo enim ipsam volutem odit voluptast aspernatur odit</h4>
    <div class="date">&#128197; Apr 28, 2019</div>
    <p>Neque porro quisquam est, qui dolorem ipsum quia dolor sit amet, consectetur, adipisci velit, sed quia non numquam eius modi</p>
  </div>
</article>
<div class="btn" style="left:480px;top:4424px;width:242px;height:48px">View all articles <span class="dot"></span></div>

<!-- Footer -->
<div class="brand" style="left:0;width:1200px;justify-content:center;top:4700px;color:#fff;font-size:34px">
  <span class="mark" style="width:36px;height:36px;background:#fff"></span>Verdana Crest
</div>

<div class="foot-col" style="left:112px;width:240px">
  <h5>Contact us</h5>
  <div class="contact-row"><span>&#9906;</span><span>48 Lantern Row, Brookfield<br>AB 40217, USA.</span></div>
  <div class="contact-row"><span>&#9742;</span><span>(+1) 555 014 2291</span></div>
  <div class="contact-row"><span>&#9993;</span><span>hello@verdanacrest.example</span></div>
</div>
<div class="foot-col" style="left:402px">
  <h5>Quick links</h5>
  <ul><li><i>&raquo;</i>Home</li><li><i>&raquo;</i>About Us</li><li><i>&raquo;</i>Our Services</li><li><i>&raquo;</i>Partner</li><li><i>&raquo;</i>Contact Us</li></ul>
</div>
<div class="foot-col" style="left:624px">
  <h5>Other links</h5>
  <ul><li><i>&raquo;</i>Careers</li><li><i>&raquo;</i>FAQ</li><li><i>&raquo;</i>Press</li><li><i>&raquo;</i>Terms &amp; Conditions</li><li><i>&raquo;</i>Privacy Policy</li></ul>
</div>
<div class="foot-col" style="left:838px;width:260px">
  <h5>Newsletter subscription</h5>
  <p style="font-size:12.5px;line-height:20px">Register your Email Address to get more Information about us</p>
  <div class="email-field">Email Address</div>
  <span class="sub-btn">SUBSCRIBE</span>
</div>

<div class="abs foot-line"></div>
<div class="abs copy">Copyrights &copy; 2019 Verdana Crest. All Rights Reserved.</div>
<div class="abs socials"><span></span><span></span><span></span><span></span></div>

</body>
</html>
```